Harbor Crestline (Business Card Design)

Need business cards designed. Something modern, chic, and sleek. Mabye the back of the card should be the navy blue that is in the logo and then just the logo on the back.

Target Market(s)

Those in the hotel, office, and renovation industry

Contact Information for Business Card

1. Logo 2. Dorian Fenwick 3. CEO/Founder 4. Phone: (833) HarbCre / (833) 427-2731 5. Email: dorian@theharborcrestline.com 6. Website: www.theharborcrestline.com

Font styles to use
Other font styles liked:
• Look at the logo font and base the font for everything else off of that.

Colors
0054AA
0677BA
7BADD7
CADEEF
E8F1F8

Requirements
Must have
• Colors that are associated in the logo
Nice to have
• Sleek modern clean and chic design.

```html
<!DOCTYPE html>
<html lang="en">
<head>
<meta charset="utf-8">
<title>Harbor Crestline — Business Card</title>
<link href="https://fonts.googleapis.com/css2?family=Montserrat:wght@400;500;600;700&family=Open+Sans:wght@400;600&display=swap" rel="stylesheet">
<style>
  :root {
    --backdrop: #2a2b2f;
    --navy: #0f1a42;
    --navy-emboss: #17244f;
    --gold: #d4a437;
    --white: #ffffff;
  }
  * { margin: 0; padding: 0; box-sizing: border-box; }
  html, body { width: 1200px; height: 947px; overflow: hidden; }
  body {
    background: var(--backdrop);
    display: flex;
    flex-direction: column;
    align-items: center;
    justify-content: center;
    gap: 48px;
    font-family: "Montserrat", sans-serif;
  }
  .card {
    width: 700px;
    height: 400px;
    background: var(--navy);
    border-radius: 26px;
    position: relative;
    box-shadow: 0 18px 40px rgba(0,0,0,0.45);
  }

  /* Back */
  .card-back { display: flex; align-items: center; justify-content: center; }
  .wordmark-emboss {
    display: flex; align-items: center; gap: 18px;
    color: var(--navy-emboss);
    font-weight: 600; font-size: 46px; letter-spacing: 4px;
    text-transform: uppercase;
    text-shadow: 0 1px 0 rgba(255,255,255,0.05), 0 -1px 0 rgba(0,0,0,0.35);
  }
  .wordmark-emboss .mark-square {
    width: 34px; height: 34px; background: var(--navy-emboss);
  }

  /* Front */
  .card-front { display: flex; align-items: center; padding: 0 52px 0 56px; }
  .brand {
    width: 250px;
    display: flex; align-items: center; gap: 12px;
  }
  .brand .mark-square { width: 22px; height: 22px; background: var(--gold); flex: none; }
  .brand .brand-name {
    color: var(--white); font-weight: 600; font-size: 22px;
    letter-spacing: 2px; text-transform: uppercase; line-height: 1.2;
  }
  .divider { width: 2px; height: 190px; background: var(--gold); margin: 0 40px 0 22px; }
  .details { color: var(--white); }
  .person-name { color: var(--gold); font-weight: 700; font-size: 30px; line-height: 1.1; }
  .person-title { font-family: "Open Sans", sans-serif; font-size: 17px; margin-top: 6px; }
  .contact-list { list-style: none; margin-top: 26px; font-family: "Open Sans", sans-serif; font-size: 15.5px; }
  .contact-list li { display: flex; align-items: center; gap: 10px; line-height: 1.75; }
  .contact-list svg { width: 14px; height: 14px; fill: var(--gold); flex: none; }
</style>
</head>
<body>
  <section class="card card-back" aria-label="Card back">
    <div class="wordmark-emboss"><span class="mark-square"></span>Harbor Crestline</div>
  </section>

  <section class="card card-front" aria-label="Card front">
    <div class="brand">
      <span class="mark-square"></span>
      <span class="brand-name">Harbor Crestline</span>
    </div>
    <div class="divider"></div>
    <div class="details">
      <h1 class="person-name">Dorian Fenwick</h1>
      <p class="person-title">Founder + CEO</p>
      <ul class="contact-list">
        <li>
          <svg viewBox="0 0 24 24" aria-hidden="true"><path d="M6.6 10.8a15.1 15.1 0 0 0 6.6 6.6l2.2-2.2a1 1 0 0 1 1-.25 11.4 11.4 0 0 0 3.6.57 1 1 0 0 1 1 1V20a1 1 0 0 1-1 1A17 17 0 0 1 3 4a1 1 0 0 1 1-1h3.5a1 1 0 0 1 1 1c0 1.25.2 2.45.57 3.6a1 1 0 0 1-.25 1z"/></svg>
          (833) 427-2731
        </li>
        <li>
          <svg viewBox="0 0 24 24" aria-hidden="true"><path d="M2 5h20v14H2zm2 2v.5l8 5 8-5V7l-8 5z"/></svg>
          dorian@theharborcrestline.com
        </li>
        <li>
          <svg viewBox="0 0 24 24" aria-hidden="true"><path d="M12 2a10 10 0 1 0 0 20 10 10 0 0 0 0-20zm6.9 6h-2.9a15 15 0 0 0-1.4-3.6A8 8 0 0 1 18.9 8zM12 4a13 13 0 0 1 1.9 4h-3.8A13 13 0 0 1 12 4zM4.3 14a8 8 0 0 1 0-4h3.4a16 16 0 0 0 0 4zm.8 2h2.9a15 15 0 0 0 1.4 3.6A8 8 0 0 1 5.1 16zM8 8H5.1a8 8 0 0 1 4.3-3.6A15 15 0 0 0 8 8zm4 12a13 13 0 0 1-1.9-4h3.8A13 13 0 0 1 12 20zm2.3-6H9.7a14 14 0 0 1 0-4h4.6a14 14 0 0 1 0 4zm.3 5.6a15 15 0 0 0 1.4-3.6h2.9a8 8 0 0 1-4.3 3.6zM16.3 14a16 16 0 0 0 0-4h3.4a8 8 0 0 1 0 4z"/></svg>
          www.theharborcrestline.com
        </li>
      </ul>
    </div>
  </section>
</body>
</html>
```